Retro Label for old fashioned soda

We need a label for soda we are having private labeled for our retro, 1950's ice cream shop www.maplefrostparlor.example I don't want the label to look like something from 2017 with a retro feel, but more like an original (possibly kinda cheesy) label you'd see from the 1950's with some of the old catch lines like "tastes great", "invigorating" or "it is refreshing!" The prominent brand should be the name of our ice cream shop, Maple Frost Parlor. the soda is also pure cane sugar so it might be good to have that on somewhere

Label size is 2.4" wide by 4" tall. Here is an example of some retro labels from findwell. I attached on file to this contest but there are more here: https://www.findwell.example/images?q=retro+soda+label&ref=Kx7Qm2Lp9Vt4Rz8Nw3Hd5Jb6Yc1Fg0TsUaWe2Pv7Xo4Ml9Qn8Bk3Dr6Zh5Cy1Ej0Gu7Ai4Ot2Sf9Lw6Nx8Mb3&w=2560&h=1470#img=Pq7Rt2Vw9Xz4Ab:

The label will be the same for all the flavors with the exception of the flavor name changing somewhere on the label. These are the flavors

Root Beer
Orange
Black Cherry
Lemonade
Raspberry Lime -Rickey
White Birch Beer
Lemon Iced Tea
Vanilla Cream
Orange Cream
Sarsaparilla
Ginger Ale

Industry/Entity Type

Shop

Colors

Designer to choose colors to be used in the design.

Requirements
Must have
• retro feel. authentic old fashioned look

```html
<!DOCTYPE html>
<html lang="en">
<head>
<meta charset="utf-8">
<title>Maple Frost Parlor – Black Cherry Soda Label</title>
<link rel="stylesheet" href="https://fonts.googleapis.com/css2?family=Rye&family=Oswald:wght@700&family=Libre+Baskerville:wght@700&family=Lobster&family=Old+Standard+TT&display=swap">
<style>
  :root {
    --backdrop: #c9d1d3;
    --cream: #ead9b0;
    --tan: #c9b184;
    --badge-green: #3f6a4c;
    --field-green: #66876a;
    --field-orange: #cf7a4f;
    --ribbon-navy: #1f3550;
    --sun-yellow: #f2c230;
    --brand-red: #c8402c;
    --ribbon-red: #9a2a2e;
    --script-red: #c8333a;
    --ink: #2a2420;
    --white: #fbf6ea;
    --crown-gold: #b8933f;
  }
  html, body {
    margin: 0;
    width: 1200px;
    height: 901px;
    overflow: hidden;
    background: var(--backdrop);
  }
  .stage {
    position: relative;
    width: 1200px;
    height: 901px;
  }
  .label {
    position: absolute;
    left: 360px;
    top: 90px;
    width: 480px;
    height: 720px;
    box-shadow: 0 6px 18px rgba(0,0,0,0.18);
  }
  .label__pattern {
    position: absolute;
    inset: 0;
    background: linear-gradient(160deg, var(--cream), var(--tan));
  }
  .label__art {
    position: absolute;
    inset: 0;
    width: 480px;
    height: 720px;
  }
  .slogan {
    font-family: "Oswald", sans-serif;
    font-weight: 700;
    font-size: 30px;
    letter-spacing: 1px;
    fill: var(--sun-yellow);
  }
  .brand-name {
    font-family: "Rye", serif;
    fill: var(--brand-red);
  }
  .flavor {
    font-family: "Libre Baskerville", serif;
    font-weight: 700;
    font-size: 24px;
    fill: var(--white);
  }
  .cane-sugar {
    font-family: "Lobster", cursive;
    font-size: 32px;
    fill: var(--script-red);
  }
  .volume {
    font-family: "Old Standard TT", serif;
    font-size: 24px;
    fill: var(--ink);
  }
</style>
</head>
<body>
<main class="stage">
  <section class="label" aria-label="Maple Frost Parlor Black Cherry soda label">
    <div class="label__pattern" role="img" aria-label="Cream and tan harlequin diamond pattern, lightly distressed"></div>
    <svg class="label__art" viewBox="0 0 480 720" xmlns="http://www.w3.org/2000/svg">
      <defs>
        <linearGradient id="badge-field" x1="0" y1="0" x2="0" y2="1">
          <stop offset="0" stop-color="var(--field-orange)"/>
          <stop offset="0.42" stop-color="var(--field-orange)"/>
          <stop offset="0.42" stop-color="var(--field-green)"/>
          <stop offset="1" stop-color="var(--field-green)"/>
        </linearGradient>
        <radialGradient id="star-burst" cx="0.5" cy="0.5" r="0.5">
          <stop offset="0" stop-color="#f6efe0"/>
          <stop offset="0.7" stop-color="#d9c9a6"/>
          <stop offset="1" stop-color="#d9c9a6" stop-opacity="0"/>
        </radialGradient>
        <path id="slogan-arc" d="M70,245 Q240,135 410,245"/>
      </defs>

      <polygon class="badge" points="240,60 430,170 430,560 240,680 50,560 50,170"
               fill="url(#badge-field)" stroke="var(--badge-green)" stroke-width="14" stroke-linejoin="round"/>

      <rect class="crown" x="212" y="36" width="56" height="36" rx="4"
            fill="var(--crown-gold)" role="img" aria-label="Small crown emblem"/>

      <g class="star-burst" role="img" aria-label="White five-pointed star with navy outline over a radiating sunburst">
        <circle cx="240" cy="390" r="150" fill="url(#star-burst)"/>
      </g>

      <path class="slogan-ribbon" d="M70,245 Q240,135 410,245" fill="none"
            stroke="var(--ribbon-navy)" stroke-width="46"/>
      <text class="slogan" text-anchor="middle" dy="10">
        <textPath href="#slogan-arc" startOffset="50%">QUENCH YOUR THIRST</textPath>
      </text>

      <text class="brand-name" x="240" y="335" text-anchor="middle" font-size="50">Maple Frost</text>
      <text class="brand-name" x="240" y="392" text-anchor="middle" font-size="44">Parlor</text>

      <rect class="flavor-ribbon" x="105" y="468" width="270" height="48" rx="6" fill="var(--ribbon-red)"/>
      <text class="flavor" x="240" y="501" text-anchor="middle">Black Cherry</text>

      <text class="cane-sugar" x="240" y="575" text-anchor="middle">Made from Pure</text>
      <text class="cane-sugar" x="240" y="612" text-anchor="middle">Cane Sugar</text>

      <text class="volume" x="28" y="650">16oz</text>
      <text class="volume" x="452" y="650" text-anchor="end">500ml</text>
    </svg>
  </section>
</main>
</body>
</html>
```